new construction company branding

branding

Can I have a banner made so I can hang it as 1) branding my jobsite 2) advertisement

Target Market(s)

Commercial

Industry/Entity Type

Construction Trade

Font styles to use
Other font styles liked:
• Cinzel bold

Colors
EB3D1F
EC4F4E
F09395
F8D3D4
FCEDEE

Requirements
Must have
• Bright colors for advertisement
Nice to have
• 36”x48” canvas
Should not have
• To busy

```html
<!DOCTYPE html>
<html lang="en">
<head>
<meta charset="utf-8">
<title>Keystone Build Co – General Contractor Flyer</title>
<link rel="stylesheet" href="https://fonts.googleapis.com/css2?family=Cinzel:wght@400;700&family=Great+Vibes&family=Questrial&family=Roboto:wght@400&family=Signika:wght@700&display=swap">
<style>
  :root {
    --red: #e10f16;
    --ink: #231f20;
    --grey-name: #6f6f6f;
    --paper: #ffffff;
    --backdrop: #ededed;
    --navy: #2c4283;
  }
  * { box-sizing: border-box; margin: 0; padding: 0; }
  html, body { width: 1200px; height: 1200px; overflow: hidden; }
  body { background: var(--backdrop); position: relative; }

  .flyer {
    position: absolute; left: 195px; top: 30px;
    width: 810px; height: 1140px;
    background: var(--paper); overflow: hidden;
    box-shadow: 0 4px 18px rgba(0,0,0,.12);
  }
  .hero-art { position: absolute; left: 0; top: 0; width: 810px; height: 720px; }

  .brand { position: absolute; left: 72px; top: 135px; }
  .brand-name {
    display: flex; align-items: center; gap: 10px;
    font-family: "Cinzel", serif; font-weight: 400; font-size: 28px;
    color: var(--grey-name); letter-spacing: .5px;
  }
  .brand-name .mark { width: 14px; height: 14px; background: var(--red); }
  .brand-tagline {
    margin-top: 12px;
    font-family: "Cinzel", serif; font-weight: 700; font-size: 20px;
    color: var(--red); letter-spacing: 6px;
  }

  .headline { position: absolute; left: 57px; top: 242px; }
  .headline .script { font-family: "Great Vibes", cursive; font-size: 34px; color: var(--ink); }
  .headline .lead { font-family: "Signika", sans-serif; font-weight: 700; font-size: 46px; color: var(--red); line-height: 1.05; margin-top: 6px; }
  .headline .sub { font-family: "Signika", sans-serif; font-weight: 700; font-size: 35px; color: var(--red); line-height: 1.2; }
  .headline .body { font-family: "Questrial", sans-serif; font-size: 31px; color: var(--ink); line-height: 1.2; margin-top: 6px; }

  .services-title { position: absolute; left: 57px; top: 552px; }
  .services-title h2 { font-family: "Signika", sans-serif; font-weight: 700; font-size: 32px; color: var(--ink); line-height: 1; }
  .services-title p { font-family: "Signika", sans-serif; font-weight: 700; font-size: 19px; color: var(--red); margin-top: 4px; }

  .service-list { position: absolute; left: 58px; top: 632px; width: 318px; list-style: none; }
  .service-list li {
    position: relative; padding-left: 26px; margin-bottom: 22px;
    font-family: "Questrial", sans-serif; font-size: 18.5px; line-height: 23px;
    color: var(--ink); text-align: justify;
  }
  .service-list li svg { position: absolute; left: 0; top: 4px; width: 16px; height: 16px; }

  .gallery {
    position: absolute; left: 405px; top: 636px;
    display: grid; grid-template-columns: 174px 174px; grid-template-rows: 186px 186px; gap: 20px 18px;
  }
  .tile-roofer { background: linear-gradient(135deg, #e9e6e1 0%, #8a7a6a 55%, #3b3f4a 100%); }
  .tile-plumber { background: linear-gradient(160deg, #f2f2f2 0%, #c9c9c9 50%, #5a5d66 100%); }
  .tile-metal-roof { background: linear-gradient(180deg, #5d8ec8 0%, #cfdbe6 38%, #b8c1cc 100%); }
  .tile-electrician { background: linear-gradient(135deg, #b07a3a 0%, #d9d9d9 45%, #3a3d44 100%); }

  .contact-bar {
    position: absolute; left: 0; top: 1063px; width: 810px; height: 48px;
    background: var(--ink); display: flex; align-items: center; gap: 18px;
    padding-left: 53px; font-family: "Roboto", sans-serif; font-size: 26px;
  }
  .contact-bar .label { color: var(--red); }
  .contact-bar .value { color: var(--paper); }
</style>
</head>
<body>
  <main class="flyer">
    <svg class="hero-art" viewBox="0 0 810 720" role="img" aria-label="Photo of a smiling contractor in a navy uniform and cap writing on a clipboard in a boiler room">
      <defs>
        <linearGradient id="heroTone" x1="0" y1="0" x2="1" y2="0">
          <stop offset="0" stop-color="#ffffff"/>
          <stop offset="0.45" stop-color="#f1f2f4"/>
          <stop offset="0.72" stop-color="#c3cbdc"/>
          <stop offset="1" stop-color="#2c4283"/>
        </linearGradient>
      </defs>
      <path d="M0,0 H810 V600 Q420,505 0,489 Z" fill="url(#heroTone)"/>
      <path d="M0,489 Q420,505 810,600 V714 Q520,545 0,495 Z" fill="var(--red)"/>
    </svg>

    <header class="brand">
      <div class="brand-name"><span>Keystone Build Co LLC</span><span class="mark"></span></div>
      <div class="brand-tagline">GENERAL CONTRACTOR</div>
    </header>

    <section class="headline">
      <p class="script">Testimonium Multitudinis</p>
      <h1 class="lead">GRAECUM ENIM</h1>
      <p class="sub">HUNC VERSUM NOSTIS</p>
      <p class="body">Suavis laborum est praet<br>Expectare nolisententia</p>
    </section>

    <section class="services-title">
      <h2>VOLUPTATES FUGIAT</h2>
      <p>sed quia maiores consequatur</p>
    </section>

    <ul class="service-list">
      <li><svg viewBox="0 0 16 16"><circle cx="8" cy="8" r="8" fill="#e10f16"/><path d="M4.3 8.2l2.5 2.4 4.9-5" stroke="#fff" stroke-width="2" fill="none"/></svg>Graecum enim hunc versum nostis omnes-: Suavis laborum est praeteritorum memoria.</li>
      <li><svg viewBox="0 0 16 16"><circle cx="8" cy="8" r="8" fill="#e10f16"/><path d="M4.3 8.2l2.5 2.4 4.9-5" stroke="#fff" stroke-width="2" fill="none"/></svg>Deque his rebus satis multa in nostris de re publica libris sunt dicta a Laelio.</li>
      <li><svg viewBox="0 0 16 16"><circle cx="8" cy="8" r="8" fill="#e10f16"/><path d="M4.3 8.2l2.5 2.4 4.9-5" stroke="#fff" stroke-width="2" fill="none"/></svg>Est enim, in quo sit cupiditas, quin recte cupidus dici possit Sed videbimus.</li>
      <li><svg viewBox="0 0 16 16"><circle cx="8" cy="8" r="8" fill="#e10f16"/><path d="M4.3 8.2l2.5 2.4 4.9-5" stroke="#fff" stroke-width="2" fill="none"/></svg>Quod iam a me expectare noli. Cuius quidem, quoniam Stoicus fuit, sententia condemnata mihi videtur esse inanitas ista Ft quidem iure fortasse,</li>
    </ul>

    <div class="gallery">
      <div class="tile-roofer" role="img" aria-label="Photo of a roofer in a hard hat working on shingles"></div>
      <div class="tile-plumber" role="img" aria-label="Photo of a plumber fixing pipes under a sink"></div>
      <div class="tile-metal-roof" role="img" aria-label="Photo of a corrugated metal roof under a blue sky"></div>
      <div class="tile-electrician" role="img" aria-label="Photo of an electrician testing a breaker panel"></div>
    </div>

    <footer class="contact-bar">
      <span><span class="label">Call Us :</span> <span class="value">012-555-0148</span></span>
      <span><span class="label">Visit Us</span> <span class="value">www.keystonebuildco.com</span></span>
    </footer>
  </main>
</body>
</html>
```